KAJU Freightways #ALLKAJU Business Cards & Letterhead

I am looking to business cards designed for our organization. We are currently undergoing a small re-branding that is taking place. Our organization is called KAJU Freightways and we are headquartered in Phoenix, AZ. We primarily provide transportation and logistics services to the Marlow Parcel Bureau who is our largest customer. I would like to see a design that incorporates name, title, contact info, website, and address (this will be different depending on the employee). I would also like to see some color on the business card using our logo colors or a variation. I would like our logo on the back of the business card with the website displayed. The final design should communicate that we are a next generation transportation operate that focuses on being driver-first, customer-centric, innovative, and sustainable.We would also like our #ALLKAJU catch phrase incorporated as well.

Target Market(s)

Transportation & Logistics

Industry/Entity Type

Trucking Company

Contact Information for Business Card

-First and Last Name
-Position Title
-Contact Phone
-Contact Email
-Physical Address

Font styles to use
Serif

Colors

Designer to choose colors to be used in the design.

Requirements
Must have
• -KAJU logo prominently displayed
• -#ALLKAJU catch phrase used
• -Some amount of color, design gradient, etc.
• -Logo on the back with website listed (https://www.kajufreightco.example)

```html
<!DOCTYPE html>
<html lang="en">
<head>
<meta charset="utf-8">
<title>KAJU Freightways – Business Card</title>
<link rel="stylesheet" href="https://fonts.googleapis.com/css2?family=Roboto+Slab:wght@400;500;700&display=swap">
<style>
  :root {
    --backdrop: #b9b9b9;
    --lime: #78b62a;
    --lime-bright: #86c232;
    --teal-dark: #0d3a40;
    --teal-mid: #2d5b57;
    --ink: #123c42;
    --paper: #f1f1f0;
    --white: #ffffff;
  }
  * { box-sizing: border-box; margin: 0; padding: 0; }
  html, body {
    width: 1200px; height: 576px; overflow: hidden;
    background: var(--backdrop);
    font-family: "Roboto Slab", Georgia, serif;
  }
  .stage { position: relative; width: 1200px; height: 576px; }
  .card {
    position: absolute; top: 139px; width: 484px; height: 293px;
    border-radius: 10px; overflow: hidden;
    box-shadow: 0 4px 10px rgba(0,0,0,0.25);
  }

  /* Back of card */
  .card-back { left: 82px; }
  .card-back .truck-photo {
    position: absolute; inset: 0;
    background: linear-gradient(125deg, var(--lime-bright) 0%, #4f9a3a 30%, var(--teal-mid) 65%, var(--teal-dark) 100%);
  }
  .card-back .brand-mark {
    position: absolute; left: 162px; top: 50px; width: 160px; height: 160px;
    border: 6px solid var(--white); border-radius: 50%;
    display: flex; align-items: center; justify-content: center;
    color: var(--white); font-weight: 700; font-size: 40px; letter-spacing: 1px;
  }
  .card-back .catchphrase {
    position: absolute; left: 0; right: 0; top: 222px; text-align: center;
    color: var(--white); font-weight: 700; font-size: 13px; letter-spacing: 3px;
  }
  .card-back .site {
    position: absolute; left: 0; right: 0; top: 262px;
    display: flex; align-items: center; justify-content: center; gap: 18px;
    color: var(--white); font-size: 12px; letter-spacing: 2.4px;
  }
  .card-back .site::before, .card-back .site::after {
    content: ""; width: 34px; height: 2px; background: var(--lime-bright);
  }

  /* Front of card */
  .card-front { left: 602px; background: var(--paper); color: var(--ink); }
  .card-front .ghost-mark {
    position: absolute; left: 276px; top: 0; width: 240px; height: 240px;
    border: 6px solid rgba(18,60,66,0.06); border-radius: 50%;
    display: flex; align-items: center; justify-content: center;
    color: rgba(18,60,66,0.06); font-weight: 700; font-size: 72px;
  }
  .card-front .brand-mark {
    position: absolute; left: 22px; top: 32px; width: 98px; height: 98px;
    border: 3px solid var(--lime); border-radius: 50%;
    display: flex; align-items: center; justify-content: center;
    color: var(--ink); font-weight: 700; font-size: 24px;
  }
  .card-front .company-name {
    position: absolute; left: 136px; top: 54px;
    font-weight: 500; font-size: 21px; line-height: 25px;
  }
  .card-front .person-name {
    position: absolute; left: 25px; top: 168px;
    font-weight: 700; font-size: 19px;
  }
  .card-front .person-title {
    position: absolute; left: 25px; top: 194px; font-size: 12px;
    padding-bottom: 4px; border-bottom: 1.5px solid var(--lime);
  }
  .card-front .address {
    position: absolute; left: 25px; top: 232px; font-size: 12px; line-height: 18px;
  }
  .card-front .contacts {
    position: absolute; left: 262px; top: 178px; list-style: none;
    font-size: 12px; line-height: 18px;
  }
  .card-front .contacts li { display: flex; align-items: center; gap: 10px; white-space: nowrap; }
  .card-front .contacts svg { width: 11px; height: 11px; fill: var(--lime); flex: none; }
  .card-front .footer-band {
    position: absolute; left: 0; bottom: 0; width: 484px; height: 36px;
  }
  .card-front .footer-label {
    position: absolute; left: 240px; width: 236px; bottom: 11px; text-align: center;
    color: var(--white); font-size: 12px; white-space: nowrap;
  }
</style>
</head>
<body>
<div class="stage">

  <section class="card card-back">
    <div class="truck-photo" role="img" aria-label="Photo of a semi truck cab under a green-to-teal colour wash"></div>
    <div class="brand-mark">KAJU</div>
    <p class="catchphrase">#ALLKAJU</p>
    <p class="site">www.kajufreightco.example</p>
  </section>

  <section class="card card-front">
    <div class="ghost-mark" aria-hidden="true">KAJU</div>
    <div class="brand-mark">KAJU</div>
    <h1 class="company-name">Transportation &amp;<br>Energy&nbsp;&nbsp;Services</h1>

    <p class="person-name">Dana Whitfield</p>
    <p class="person-title">Chairman &amp; CEO</p>
    <p class="address">4120 North Cedar Ridge<br>Parkway Mesa, AZ 85201</p>

    <ul class="contacts">
      <li><svg viewBox="0 0 12 12"><path d="M1 3c0-1 1-2 2-2h6c1 0 2 1 2 2v1H8V3H4v1H1zM2 5h8l1 6H1z"/></svg>555-014-0677</li>
      <li><svg viewBox="0 0 12 12"><path d="M0 2h12v8H0zM1 3l5 4 5-4v-.2H1z" fill-rule="evenodd"/></svg>dana@kajufreightco.example</li>
      <li><svg viewBox="0 0 12 12"><circle cx="6" cy="6" r="5.5"/><path d="M0.5 6h11M6 .5v11M2 3h8M2 9h8" stroke="#f1f1f0" stroke-width=".8" fill="none"/></svg>www.kajufreightco.example</li>
    </ul>

    <svg class="footer-band" viewBox="0 0 484 36" preserveAspectRatio="none" aria-hidden="true">
      <polygon points="0,30 225,30 225,36 0,36" fill="var(--lime)"/>
      <polygon points="232,0 484,0 484,36 214,36" fill="var(--teal-dark)"/>
    </svg>
    <p class="footer-label">KAJU Freightways &amp; Energy</p>
  </section>

</div>
</body>
</html>
```